Quillmarsh Property Solutions need a business card design

Hello guys. We would need a business card design asap please.
We are a start up property investment business based in London UK specialised in buying, selling, managing and letting properties and helping distressed property owners.
The name of our Business is Quillmarsh, the logo symbolises the four fundamental elements of the world (earth, air, fire and water) and so it stands for strength, stability, longevity.
We would like the business card to communicate professionalism and reliability. Many many thanks indeed for your work.

Details:

1.) Rosalind Updike
Property Investor
Mobile: +44(0)7700123456
Email: rosalind.quillmarsh@mailbox-example.com

2.) Dominic Updike
Property Investor
Mobile: +44(0)7700987654
Email: dominic.quillmarsh@mailbox-example.com

```html
<!DOCTYPE html>
<html lang="en">
<head>
<meta charset="utf-8">
<title>Quillmarsh Property Solutions – Business Card</title>
<link rel="stylesheet" href="https://fonts.googleapis.com/css2?family=Open+Sans:wght@400;600;700&display=swap">
<style>
  :root {
    --page-bg: #e6e8ec;
    --brand-blue: #1a5fcf;
    --brand-blue-light: #3f86e6;
    --brand-red: #d1242e;
    --card-white: #ffffff;
    --text-grey: #8a8a8a;
    --text-dark: #333333;
    --card-shadow: 0 12px 30px rgba(30, 40, 60, 0.18);
  }
  * { box-sizing: border-box; margin: 0; padding: 0; }
  html, body {
    width: 1200px;
    height: 987px;
    overflow: hidden;
    background: var(--page-bg);
    font-family: "Open Sans", Arial, sans-serif;
  }
  .sheet {
    width: 1200px;
    height: 987px;
    display: flex;
    flex-direction: column;
    align-items: center;
    justify-content: center;
    gap: 60px;
  }
  .card {
    position: relative;
    width: 680px;
    height: 400px;
    border-radius: 26px;
    overflow: hidden;
    box-shadow: var(--card-shadow);
  }

  /* Back of card */
  .card-back {
    background: radial-gradient(circle at 52% 42%, var(--brand-blue-light) 0%, var(--brand-blue) 62%);
    display: flex;
    flex-direction: column;
    align-items: center;
    justify-content: center;
    gap: 26px;
  }
  .back-brand {
    display: flex;
    align-items: center;
    gap: 16px;
  }
  .brand-square {
    width: 34px;
    height: 34px;
    background: var(--card-white);
  }
  .back-brand .brand-name {
    font-size: 46px;
    font-weight: 700;
    color: var(--card-white);
    letter-spacing: 3px;
    text-transform: uppercase;
  }
  .website {
    font-size: 22px;
    color: var(--card-white);
    letter-spacing: 3px;
  }

  /* Front of card */
  .card-front { background: var(--card-white); }
  .front-curves {
    position: absolute;
    inset: 0;
  }
  .front-brand {
    position: absolute;
    left: 250px;
    top: 62px;
  }
  .front-brand .brand-row {
    display: flex;
    align-items: center;
    gap: 14px;
  }
  .front-brand .brand-square {
    width: 28px;
    height: 28px;
    background: var(--brand-blue);
  }
  .front-brand .brand-name {
    font-size: 38px;
    font-weight: 700;
    color: var(--text-grey);
    letter-spacing: 1px;
    text-transform: uppercase;
  }
  .tagline {
    margin: 2px 0 0 42px;
    font-size: 14px;
    font-weight: 600;
    color: var(--text-grey);
    letter-spacing: 2px;
    text-transform: uppercase;
  }
  .person {
    position: absolute;
    left: 150px;
    top: 176px;
    font-size: 24px;
    color: var(--text-dark);
  }
  .person-name {
    font-weight: 700;
    color: var(--brand-blue);
  }
  .person-role { font-weight: 400; }
  .contact {
    position: absolute;
    left: 34px;
    bottom: 30px;
    display: flex;
    gap: 24px;
    font-size: 16px;
    color: var(--card-white);
    white-space: nowrap;
  }
  .contact-item {
    display: flex;
    align-items: center;
    gap: 8px;
  }
  .contact-item svg { display: block; }
</style>
</head>
<body>
<main class="sheet">

  <section class="card card-back" aria-label="Business card back">
    <div class="back-brand">
      <span class="brand-square"></span>
      <span class="brand-name">Quillmarsh</span>
    </div>
    <p class="website">www.quillmarsh-example.com</p>
  </section>

  <section class="card card-front" aria-label="Business card front">
    <svg class="front-curves" width="680" height="400" viewBox="0 0 680 400" aria-hidden="true">
      <path d="M0,206 C220,260 460,310 680,314" fill="none" stroke="var(--brand-red)" stroke-width="7"/>
      <path d="M0,226 C220,280 460,326 680,330 L680,400 L0,400 Z" fill="var(--brand-blue)"/>
    </svg>

    <div class="front-brand">
      <div class="brand-row">
        <span class="brand-square"></span>
        <span class="brand-name">Quillmarsh</span>
      </div>
      <p class="tagline">Property Solutions</p>
    </div>

    <p class="person">
      <span class="person-name">Rosalind Updike,</span>
      <span class="person-role">Property Investor</span>
    </p>

    <div class="contact">
      <span class="contact-item">
        <svg width="12" height="18" viewBox="0 0 12 18" aria-hidden="true">
          <rect x="1" y="1" width="10" height="16" rx="2" fill="none" stroke="#fff" stroke-width="1.6"/>
          <rect x="3" y="3.5" width="6" height="6" fill="#fff"/>
          <circle cx="6" cy="13.5" r="1.3" fill="#fff"/>
        </svg>
        +44(0)7700123456
      </span>
      <span class="contact-item">
        <svg width="18" height="13" viewBox="0 0 18 13" aria-hidden="true">
          <rect x="1" y="1" width="16" height="11" rx="1.5" fill="none" stroke="#fff" stroke-width="1.6"/>
          <path d="M1.5,1.5 L9,7.5 L16.5,1.5" fill="none" stroke="#fff" stroke-width="1.6"/>
        </svg>
        rosalind.quillmarsh@mailbox-example.com
      </span>
    </div>
  </section>

</main>
</body>
</html>
```